Pine Hollow Haven Home Inc. Website Update

We have a couple of broken links such as the "contact us" and would like to add board members and a calendar of events. We are open to a new design.

```html
<!DOCTYPE html>
<html lang="en">
<head>
<meta charset="utf-8">
<title>Pine Hollow Haven Home</title>
<link rel="stylesheet" href="https://fonts.googleapis.com/css2?family=Titillium+Web:wght@300;400;600;700&family=Open+Sans:wght@400;600;700&family=Oswald:wght@400;500&display=swap">
<style>
:root{
  --navy:#1d2f4f;
  --pink:#d8467e;
  --blue:#3e8fe0;
  --gold:#f6e3a6;
  --gold-deep:#d9a928;
  --cream:#f4efe3;
  --ink:#222;
  --line:#cfcfcf;
  --footer:#eeeeee;
  --white:#fff;
  --head:"Titillium Web",sans-serif;
  --body:"Open Sans",sans-serif;
  --cond:"Oswald",sans-serif;
}
*{box-sizing:border-box;margin:0;padding:0}
html,body{width:1200px;height:5000px;overflow:hidden}
body{position:relative;background:var(--white);font-family:var(--body);color:var(--ink)}
.abs{position:absolute}
.btn{display:flex;align-items:center;justify-content:center;font-family:var(--body);font-weight:600;text-transform:uppercase;letter-spacing:.5px}

/* header */
.site-header{left:0;top:0;width:1200px;height:140px;background:var(--white)}
.brand{left:150px;top:22px;display:flex;align-items:center;gap:12px}
.brand-dot{width:44px;height:44px;border-radius:50%;background:var(--pink)}
.brand-name{font-family:var(--head);font-weight:700;font-size:22px;color:var(--navy);line-height:1.05;width:150px}
.call{left:665px;top:20px;display:flex;align-items:center;gap:12px}
.call-icon{width:40px;height:40px;border:2px solid var(--navy);border-radius:50%;display:flex;align-items:center;justify-content:center}
.call small{display:block;font-size:15px;color:var(--ink)}
.call strong{font-family:var(--head);font-size:26px;color:var(--navy);line-height:1}
.donate-top{left:885px;top:30px;width:172px;height:42px;border:2px solid var(--navy);font-size:14px;color:var(--navy);gap:8px}
.main-nav{left:330px;top:92px;display:flex;gap:24px;font-family:var(--body);font-weight:600;font-size:14px;text-transform:uppercase;color:var(--navy)}

/* hero */
.hero{left:0;top:140px;width:1200px;height:595px;background:linear-gradient(180deg,#7a6a52 0%,#8f8a6a 35%,#5f8a3c 70%,#3f6a28 100%)}
.hero-title{left:0;top:270px;width:1200px;text-align:center;color:var(--white);font-family:var(--head);font-weight:700;line-height:1.1}
.hero-title .l1{font-size:60px;text-transform:uppercase}
.hero-title .l2{font-size:58px;font-weight:600}
.hero-btn{left:495px;top:428px;width:210px;height:48px;background:var(--blue);border-radius:24px;color:var(--white);font-size:16px}
.dots{left:565px;top:662px;display:flex;gap:8px}
.dots i{width:12px;height:12px;border-radius:50%;background:var(--white);opacity:.75}
.dots i:first-child{opacity:1;border:2px solid var(--navy)}

/* features band */
.features{left:0;top:735px;width:1200px;height:305px;background:linear-gradient(90deg,var(--cream),#efe7d2 60%,#f5e4a8)}
.feature{top:0;width:320px;text-align:center}
.feature h3{font-family:var(--head);font-size:26px;font-weight:700;color:var(--navy);text-transform:uppercase;margin:6px 0 8px}
.feature p{font-size:14px;line-height:1.55;color:#333}
.feature-donate{left:60px;top:30px}
.feature-cert{left:810px;top:30px}
.donate-mini{margin:12px auto 0;width:150px;height:36px;border:2px solid var(--navy);font-size:13px;color:var(--navy);gap:6px}
.cert-badge{width:80px;height:80px;border-radius:50%;background:var(--gold-deep);margin:0 auto}
.stories{left:438px;top:-10px;width:324px;height:324px;border-radius:50%;background:var(--white);border:6px solid #cfe0f4;box-shadow:0 0 0 2px var(--blue) inset;display:flex;flex-direction:column;align-items:center;justify-content:center;text-align:center}
.stories .brand-dot{width:90px;height:90px;margin-bottom:14px}
.stories p{font-family:var(--head);font-size:27px;line-height:1.15;color:#222;width:230px}

/* welcome */
.welcome-frame{left:138px;top:1157px;width:393px;height:323px;border:2px solid var(--navy)}
.welcome-photo{left:150px;top:1170px;width:395px;height:320px;background:linear-gradient(135deg,#9a5a44,#b38b6a 55%,#7f8d9a)}
.welcome-text{left:600px;top:1170px;width:470px}
.welcome-text h2{font-family:var(--head);font-weight:400;font-size:34px;color:#222;line-height:1.1}
.welcome-text h2 strong{display:block;font-weight:700;color:var(--navy);text-transform:uppercase}
.welcome-text p{margin-top:18px;font-size:14px;line-height:1.85;color:#555}
.read-more{margin-top:22px;width:128px;height:38px;border:2px solid var(--navy);font-size:13px;color:var(--navy)}

/* about services */
.heart{left:582px;top:1570px}
.about-title{left:0;top:1622px;width:1200px;text-align:center;font-family:var(--head);font-weight:700;font-size:34px;color:#111;text-transform:uppercase}
.about-sub{left:0;top:1685px;width:1200px;text-align:center;font-size:15px;color:#444}
.dark-band{left:0;top:1990px;width:1200px;height:760px}
.service{width:222px;text-align:center}
.service-photo{width:222px;height:185px}
.service-body{padding:28px 14px 18px;position:relative;height:200px}
.service-body.gold{background:var(--gold)}
.service-body.white{background:var(--white);box-shadow:0 2px 6px rgba(0,0,0,.15)}
.service-icon{position:absolute;left:86px;top:-25px;width:50px;height:50px;border-radius:50%;background:var(--white);border:2px solid #ddd;display:flex;align-items:center;justify-content:center}
.service h4{font-family:var(--head);font-weight:700;font-size:17px;line-height:1.2;text-transform:uppercase;color:#222;margin:16px 0 10px}
.service p{font-size:13px;line-height:1.55;color:#333}
.s1{left:130px;top:1775px}.s2{left:368px;top:1815px}.s3{left:610px;top:1775px}.s4{left:850px;top:1815px}

/* board */
.board-title{left:0;top:2262px;width:1200px;text-align:center;font-family:var(--head);font-weight:700;font-size:38px;color:var(--white);text-transform:uppercase}
.member{top:2425px;width:292px;height:215px;border:2px solid var(--white);text-align:center;padding:52px 22px 0;color:var(--white)}
.member p{font-size:14px;line-height:1.6}
.member h5{font-family:var(--head);font-weight:700;font-size:17px;margin-top:12px}
.avatar{top:2368px;width:104px;height:104px;border-radius:50%;border:5px solid var(--white);background:linear-gradient(160deg,#c99a72,#7a4e36)}
.m1{left:145px}.m2{left:455px}.m3{left:765px}
.a1{left:239px}.a2{left:549px}.a3{left:859px}

/* events */
.events-title{left:0;top:2810px;width:1200px;text-align:center;font-family:var(--head);font-size:44px;color:#111}
.events-title strong{font-weight:700}
.events-title span{font-weight:400}
.filter-bar{left:145px;top:2922px;width:910px;height:76px;border:1px solid var(--line);display:flex;align-items:center;padding:0 24px}
.filter-month{font-family:var(--head);font-size:26px;color:#111;display:flex;align-items:center;gap:22px}
.filter-right{margin-left:auto;display:flex;gap:14px;align-items:center}
.select{height:34px;border:1px solid var(--line);font-size:14px;display:flex;align-items:center;justify-content:space-between;padding:0 10px;gap:18px}
.show-btn{width:94px;height:36px;background:#111;color:var(--white);font-size:14px;text-transform:none;font-weight:400}
.event{top:3035px;width:298px;height:300px}
.event .photo{position:absolute;inset:0}
.event .shade{position:absolute;left:0;right:0;bottom:0;height:140px;background:linear-gradient(180deg,rgba(0,0,0,0),rgba(0,0,0,.78))}
.event .date{position:absolute;left:18px;top:200px;background:var(--gold);padding:4px 10px;font-size:12px;color:#222;display:flex;gap:6px;align-items:center}
.event h6{position:absolute;left:18px;right:14px;top:236px;font-family:var(--cond);font-weight:400;font-size:16px;line-height:1.25;color:var(--white);text-transform:uppercase}
.e1{left:145px}.e2{left:452px}.e3{left:760px}
.arrow{top:3165px}

/* join */
.join{left:0;top:3475px;width:1200px;height:415px;background:linear-gradient(90deg,#5a86c4 0%,#7ea1d2 55%,#a9c0e2 100%)}
.join-person{left:840px;top:3475px;width:300px;height:415px;background:linear-gradient(180deg,#e6c9a8,#d9d5d0 45%,#f2f2f2)}
.join-text{left:142px;top:3545px;color:var(--white)}
.join-text h2{font-family:var(--head);font-weight:700;font-size:40px;text-transform:uppercase}
.join-text p{font-family:var(--head);font-weight:600;font-size:17px;line-height:1.75}
.join-input{left:145px;top:3728px;width:466px;height:48px;background:var(--white);font-size:14px;color:#555;padding:0 16px;display:flex;align-items:center}
.join-btn{left:145px;top:3785px;width:466px;height:50px;background:#e9e9e9;color:#111;font-size:17px;font-weight:700}

/* reviews */
.reviews-title{left:0;top:4005px;width:1200px;text-align:center;font-family:var(--head);font-weight:700;font-size:40px;color:#111}
.reviews-text{left:210px;top:4085px;width:780px;text-align:center;font-size:14px;line-height:1.85;color:#555}
.r-av{border-radius:50%;background:linear-gradient(160deg,#c8a184,#6e5445);border:3px solid var(--white);box-shadow:0 0 0 1px #ccc}
.r1{left:460px;top:4218px;width:70px;height:70px}
.r2{left:555px;top:4200px;width:90px;height:90px}
.r3{left:670px;top:4218px;width:70px;height:70px}
.r-name{left:0;top:4312px;width:1200px;text-align:center;font-size:17px;color:#333}
.quote{top:4298px;font-family:var(--head);font-size:50px;color:#bbb}
.r-dots{left:576px;top:4378px;display:flex;gap:6px}
.r-dots i{width:14px;height:14px;border-radius:50%;border:2px solid #333}
.r-dots i:first-child{background:#333}

/* footer */
.footer{left:0;top:4480px;width:1200px;height:385px;background:var(--footer)}
.f-col h3{font-family:var(--head);font-weight:700;font-size:24px;color:#111;text-transform:uppercase;margin-bottom:22px}
.f-contact{left:140px;top:4535px;width:240px}
.f-row{display:flex;gap:16px;font-size:14px;line-height:1.45;color:#333;margin-bottom:16px}
.f-form{left:430px;top:4535px;width:420px}
.fields{display:grid;grid-template-columns:208px 208px;gap:10px 10px}
.field{height:40px;background:var(--white);border:1px solid #ddd;font-size:12px;color:#555;padding:0 10px;display:flex;align-items:center}
.f-actions{display:flex;align-items:center;gap:34px;margin-top:12px}
.submit{width:208px;height:40px;background:#111;color:var(--white);font-size:15px}
.socials{display:flex;gap:8px}
.socials i{width:36px;height:36px;border-radius:50%;border:2px solid #333}
.f-links{left:925px;top:4535px}
.f-links ul{list-style:none;font-size:14px;line-height:1.7;color:#333}
.f-links li::before{content:"› ";color:#777}
.bottom-bar{left:0;top:4900px;width:1200px;text-align:center;font-size:14px;color:#444}
</style>
</head>
<body>

<header class="abs site-header">
  <div class="abs brand"><span class="brand-dot"></span><span class="brand-name">Pine Hollow Haven Home</span></div>
  <div class="abs call">
    <span class="call-icon"><svg width="20" height="20" viewBox="0 0 24 24"><path d="M6.6 10.8c1.4 2.8 3.8 5.1 6.6 6.6l2.2-2.2c.3-.3.7-.4 1-.2 1.1.4 2.3.6 3.6.6.6 0 1 .4 1 1V20c0 .6-.4 1-1 1C10.6 21 3 13.4 3 4c0-.6.4-1 1-1h3.5c.6 0 1 .4 1 1 0 1.3.2 2.5.6 3.6.1.3 0 .7-.2 1z" fill="#1d2f4f"/></svg></span>
    <div><small>Call us</small><strong>770.555.0142</strong></div>
  </div>
  <div class="abs btn donate-top"><svg width="14" height="13" viewBox="0 0 24 22"><path d="M12 21 2 11a6 6 0 0 1 10-7 6 6 0 0 1 10 7z" fill="#1d2f4f"/></svg>Donate Now</div>
  <nav class="abs main-nav"><span>Home</span><span>About</span><span>How You Can Help</span><span>Services Offered</span><span>Our Love of Pets</span><span>Haven Walk</span><span>Contact</span></nav>
</header>

<section class="abs hero" role="img" aria-label="Photo of young women studying together on the grass"></section>
<h1 class="abs hero-title"><span class="l1">Pine Hollow</span><br><span class="l2">Haven Home</span></h1>
<div class="abs btn hero-btn">Get More Info</div>
<div class="abs dots"><i></i><i></i><i></i><i></i></div>

<section class="abs features">
  <div class="abs feature feature-donate">
    <svg width="48" height="44" viewBox="0 0 48 44"><circle cx="26" cy="12" r="10" fill="none" stroke="#1d2f4f" stroke-width="2.5"/><text x="26" y="17" text-anchor="middle" font-family="Open Sans,sans-serif" font-size="13" font-weight="700" fill="#1d2f4f">$</text><path d="M4 32h10l8 4h12l8-6" fill="none" stroke="#1d2f4f" stroke-width="2.5" stroke-linecap="round"/></svg>
    <h3>Donate</h3>
    <p>We appreciate donations from our community! It is because of the hearts of those around us that we're able to do what we do.</p>
    <div class="btn donate-mini"><svg width="12" height="11" viewBox="0 0 24 22"><path d="M12 21 2 11a6 6 0 0 1 10-7 6 6 0 0 1 10 7z" fill="#1d2f4f"/></svg>Donate Now</div>
  </div>
  <div class="abs stories"><span class="brand-dot"></span><p>Over 500 success stories &amp; growing strong</p></div>
  <div class="abs feature feature-cert">
    <div class="cert-badge"></div>
    <h3>CRFA</h3>
    <p>Council for Residential Facility Accreditation. Facilities certified since 2009. To learn more about our CRFA accreditation, please visit www.crfa-example.org</p>
  </div>
</section>

<div class="abs welcome-frame"></div>
<div class="abs welcome-photo" role="img" aria-label="Photo of girls sitting on brick steps outside a building"></div>
<section class="abs welcome-text">
  <h2>Welcome to <strong>Pine Hollow Haven Home</strong></h2>
  <p>Sed ut perspiciatis unde omnis iste natus error sit voluptatem accusantium doloremque laudantium, totam rem aperiam, eaque ipsa quae ab illo inventore veritatis et quasi architecto beatae vitae dicta sunt explicabo. Nemo enim ipsam voluptatem quia voluptas sit aspernatur aut odit aut fugit, sed quia consequuntur</p>
  <div class="btn read-more">Read More</div>
</section>

<svg class="abs heart" width="36" height="30" viewBox="0 0 36 30"><path d="M18 27 5 14a7 7 0 0 1 13-8 7 7 0 0 1 13 8z" fill="none" stroke="#1d2f4f" stroke-width="2.5"/></svg>
<h2 class="abs about-title">We Are Pine Hollow Haven Home</h2>
<p class="abs about-sub">With the help of our community, we have raised over 1000 girls and counting! Some of the services we offer include:</p>

<svg class="abs dark-band" viewBox="0 0 1200 760" preserveAspectRatio="none"><path d="M0 30 Q300 -10 600 40 T1200 10 V760 H0z" fill="#22365a"/></svg>

<article class="abs service s1">
  <div class="service-photo" role="img" aria-label="Photo of a smiling young woman" style="background:linear-gradient(150deg,#c49a6c,#8a6a4a)"></div>
  <div class="service-body gold"><span class="service-icon"><svg width="22" height="22" viewBox="0 0 24 24"><path d="M3 11 12 3l9 8v10H3z" fill="#1d2f4f"/></svg></span><h4>Room, Board, and Watchful Oversight</h4><p>Sed ut perspiciatis unde omnis iste natus error sit voluptatem accusantium dolorem</p></div>
</article>
<article class="abs service s2">
  <div class="service-photo" role="img" aria-label="Photo of two women talking" style="background:linear-gradient(150deg,#e0d6c4,#9f8a72)"></div>
  <div class="service-body white"><span class="service-icon"><svg width="22" height="22" viewBox="0 0 24 24"><path d="M4 20c2-6 14-6 16 0M12 12a4 4 0 1 0 0-8 4 4 0 0 0 0 8z" fill="#1d2f4f"/></svg></span><h4>Transitional Living Services</h4><p>Sed ut perspiciatis unde omnis iste natus error sit voluptatem accusantium dolorem</p></div>
</article>
<article class="abs service s3">
  <div class="service-photo" role="img" aria-label="Photo of a group of students outdoors" style="background:linear-gradient(150deg,#6a9a4a,#3c5e2a)"></div>
  <div class="service-body gold"><span class="service-icon"><svg width="22" height="22" viewBox="0 0 24 24"><path d="M4 21V9l8-6 8 6v12h-6v-6h-4v6z" fill="#1d2f4f"/></svg></span><h4>Independent Living Services</h4><p>Sed ut perspiciatis unde omnis iste natus error sit voluptatem accusantium dolorem</p></div>
</article>
<article class="abs service s4">
  <div class="service-photo" role="img" aria-label="Photo of girls gathered on the lawn" style="background:linear-gradient(150deg,#7aa850,#3f6a2e)"></div>
  <div class="service-body white"><span class="service-icon"><svg width="22" height="22" viewBox="0 0 24 24"><path d="M3 10h18v4H3zM5 14h14v7H5zM12 10v11M12 10C9 4 5 6 8 10M12 10c3-6 7-4 4 0" fill="none" stroke="#1d2f4f" stroke-width="2"/></svg></span><h4>Foster<br>Gift Shop</h4><p>Sed ut perspiciatis unde omnis iste natus error sit voluptatem accusantium dolorem</p></div>
</article>

<h2 class="abs board-title">Board Members</h2>
<div class="abs member m1"><p>Sed ut perspiciatis unde omnis iste natus error sit voluptatem accusantium doloremque laudantium, totam rem aperiam, eaque ipsa quae ab</p><h5>Marlowe, J.</h5></div>
<div class="abs member m2"><p>Sed ut perspiciatis unde omnis iste natus error sit voluptatem accusantium doloremque laudantium, totam rem aperiam, eaque ipsa quae ab</p><h5>Marlowe, J.</h5></div>
<div class="abs member m3"><p>Sed ut perspiciatis unde omnis iste natus error sit voluptatem accusantium doloremque laudantium, totam rem aperiam, eaque ipsa quae</p><h5>Marlowe, J.</h5></div>
<div class="abs avatar a1" role="img" aria-label="Portrait photo of board member"></div>
<div class="abs avatar a2" role="img" aria-label="Portrait photo of board member"></div>
<div class="abs avatar a3" role="img" aria-label="Portrait photo of board member"></div>

<h2 class="abs events-title"><strong>Event</strong> <span>Calendar</span></h2>
<div class="abs filter-bar">
  <div class="filter-month">February <svg width="10" height="16" viewBox="0 0 10 16"><path d="M1 6l4-4 4 4M1 10l4 4 4-4" fill="none" stroke="#333" stroke-width="1.5"/></svg></div>
  <div class="filter-right">
    <div class="select" style="width:118px">February <svg width="8" height="6" viewBox="0 0 8 6"><path d="M0 0h8L4 6z" fill="#333"/></svg></div>
    <div class="select" style="width:88px">2019 <svg width="8" height="6" viewBox="0 0 8 6"><path d="M0 0h8L4 6z" fill="#333"/></svg></div>
    <div class="btn show-btn">Show</div>
  </div>
</div>
<svg class="abs arrow" style="left:82px" width="20" height="34" viewBox="0 0 20 34"><path d="M17 2 3 17l14 15" fill="none" stroke="#bbb" stroke-width="3"/></svg>
<svg class="abs arrow" style="left:1100px" width="20" height="34" viewBox="0 0 20 34"><path d="M3 2l14 15L3 32" fill="none" stroke="#bbb" stroke-width="3"/></svg>
<article class="abs event e1"><div class="photo" role="img" aria-label="Photo of smiling students holding books" style="background:linear-gradient(150deg,#6a4a7a,#b2826a)"></div><div class="shade"></div><div class="date">&#9638; February 17, 2019</div><h6>Sed ut perspiciatis unde omnis iste natus error sit voluptatem accusantium</h6></article>
<article class="abs event e2"><div class="photo" role="img" aria-label="Photo of a woman in business attire" style="background:linear-gradient(150deg,#d8d8d8,#4a4a4a)"></div><div class="shade"></div><div class="date">&#9638; February 17, 2019</div><h6>Sed ut perspiciatis unde omnis iste natus error sit voluptatem accusantium</h6></article>
<article class="abs event e3"><div class="photo" role="img" aria-label="Photo of a woman at a desk" style="background:linear-gradient(150deg,#5a2a2a,#2a1a1a)"></div><div class="shade"></div><div class="date">&#9638; February 17, 2019</div><h6>Sed ut perspiciatis unde omnis iste natus error sit voluptatem accusantium</h6></article>

<section class="abs join" role="img" aria-label="Faded photo of a residential building"></section>
<div class="abs join-person" role="img" aria-label="Photo of an excited woman holding a laptop"></div>
<div class="abs join-text">
  <h2>Join Our Team!</h2>
  <p>Overnight Shift House Parent<br>Maple Ridge, GA | Temporary | Salary: $11.00 /hour<br>Direct Care Worker (DCW) Maple Ridge, GA | Full-time</p>
</div>
<div class="abs join-input">Enter your E - mail</div>
<div class="abs btn join-btn">Subscribe</div>

<h2 class="abs reviews-title">Customers Reviews</h2>
<p class="abs reviews-text">Sed ut perspiciatis unde omnis iste natus error sit voluptatem accusantium doloremque laudantium, totam rem aperiam, eaque ipsa quae ab illo inventore veritatis et quasi architecto beatae vitae dicta sunt explicabo. Nemo enim ipsam voluptatem quia voluptas sit aspernatur aut odit aut fugit Sed ut perspiciatis unde omnis</p>
<div class="abs r-av r1" role="img" aria-label="Reviewer portrait photo"></div>
<div class="abs r-av r2" role="img" aria-label="Reviewer portrait photo"></div>
<div class="abs r-av r3" role="img" aria-label="Reviewer portrait photo"></div>
<span class="abs quote" style="left:490px">&ldquo;</span>
<p class="abs r-name">Blandit Lectus</p>
<span class="abs quote" style="left:675px">&rdquo;</span>
<div class="abs r-dots"><i></i><i></i><i></i></div>

<footer class="abs footer"></footer>
<div class="abs f-col f-contact">
  <h3>Contact Us</h3>
  <div class="f-row"><svg width="14" height="18" viewBox="0 0 14 20"><path d="M7 0a7 7 0 0 1 7 7c0 5-7 13-7 13S0 12 0 7a7 7 0 0 1 7-7zm0 4a3 3 0 1 0 0 6 3 3 0 0 0 0-6z" fill="#222"/></svg><span>418 Birchwood Lane,<br>Maple Ridge, GA 30199, USA</span></div>
  <div class="f-row"><svg width="14" height="16" viewBox="0 0 24 24"><path d="M6.6 10.8c1.4 2.8 3.8 5.1 6.6 6.6l2.2-2.2c.3-.3.7-.4 1-.2 1.1.4 2.3.6 3.6.6.6 0 1 .4 1 1V20c0 .6-.4 1-1 1C10.6 21 3 13.4 3 4c0-.6.4-1 1-1h3.5c.6 0 1 .4 1 1 0 1.3.2 2.5.6 3.6.1.3 0 .7-.2 1z" fill="#222"/></svg><span>Phone :<br>770.555.0142</span></div>
  <div class="f-row"><svg width="16" height="12" viewBox="0 0 16 12"><path d="M0 0h16v12H0z" fill="#222"/><path d="M0 0l8 6 8-6" fill="none" stroke="#eee" stroke-width="1.4"/></svg><span>Email:<br>info@pinehollowhaven.org</span></div>
</div>
<div class="abs f-col f-form">
  <h3>Get a Quick Now!</h3>
  <div class="fields"><div class="field">Your Name</div><div class="field">Your E - Mail</div><div class="field">Your Phone</div><div class="field">Message</div></div>
  <div class="f-actions"><div class="btn submit">Submit</div><div class="socials"><i></i><i></i><i></i><i></i></div></div>
</div>
<div class="abs f-col f-links">
  <h3>Quick Link</h3>
  <ul><li>Home</li><li>About</li><li>How You Can Help</li><li>Services Offered</li><li>Our Love of Pets</li><li>Contact Us</li><li>Haven Walk</li></ul>
</div>
<p class="abs bottom-bar">©2019 Pine Hollow Haven Home Inc. All Rights Reserved. Disclaimer &nbsp;|&nbsp; Privacy policy &nbsp;|&nbsp; Terms of use</p>

</body>
</html>
```